Banner design

Hi, looking for a banner 728 px wide and 200 px high
Could we have our 10 year logo, a similar look and feel of our previous banner design (I've attached) and also include an aboriginal design with the Wording
This email comes to you from Gubbi Gubbi country
I've attached an example of aboriginal designs.
Can we have the background of banner the Blue colour of our Maple & Fern logo and

Target Market(s)

families

Requirements
Must have
• the colours of the maple and fern logo and similar look and feel of the maple and fern banner in the example

```html
<!DOCTYPE html>
<html lang="en">
<head>
<meta charset="utf-8">
<title>Maple &amp; Fern – Gubbi Gubbi Country email banner</title>
<link rel="stylesheet" href="https://fonts.googleapis.com/css2?family=Fredoka:wght@700&family=Poppins:wght@400;600;700&display=swap">
<style>
  :root {
    --page-bg: #ebebeb;
    --banner-blue: #0b6fdc;
    --banner-blue-deep: #0a5fcc;
    --banner-blue-light: #1a86ee;
    --stripe-green: #8ed63a;
    --footer-white: #ffffff;
    --ink: #1c1c1c;
    --title-yellow: #ffd000;
    --title-orange: #ff7a0a;
    --icon-orange: #f0822a;
    --logo-yellow: #ffe400;
    --gold-light: #f3d46a;
    --gold-deep: #b98a1c;
    --art-ochre: #f0b92a;
    --art-tan: #dfae7c;
    --art-clay: #c9684e;
    --art-green: #6f9a2a;
  }
  * { box-sizing: border-box; margin: 0; padding: 0; }
  html, body {
    width: 828px; height: 1200px; overflow: hidden;
    background: var(--page-bg);
  }
  .banner {
    position: absolute; left: 40px; top: 497px;
    width: 748px; height: 206px; overflow: hidden;
    background: var(--footer-white);
    box-shadow: 0 6px 18px rgba(0,0,0,.22);
  }
  .banner__sky {
    position: absolute; left: 0; top: 0; width: 748px; height: 140px;
    background:
      radial-gradient(ellipse at 45% 10%, var(--banner-blue-light) 0%, transparent 60%),
      linear-gradient(100deg, var(--banner-blue-deep) 0%, var(--banner-blue) 45%, var(--banner-blue-deep) 100%);
  }
  .banner__stripe {
    position: absolute; left: 0; top: 140px; width: 540px; height: 7px;
    background: var(--stripe-green);
  }
  .brand {
    position: absolute; left: 24px; top: 26px; width: 86px;
    display: flex; flex-direction: column; align-items: center; gap: 6px;
  }
  .brand__dot {
    width: 40px; height: 40px; border-radius: 50%;
    background: var(--logo-yellow);
  }
  .brand__name {
    font-family: "Poppins", sans-serif; font-weight: 700;
    font-size: 17px; line-height: 18px; text-align: center;
    color: var(--logo-yellow);
  }
  .intro {
    position: absolute; left: 126px; top: 30px;
    font-family: "Poppins", sans-serif; font-weight: 400;
    font-size: 30px; line-height: 31px; color: #ffffff;
    letter-spacing: -0.3px;
  }
  .title {
    position: absolute; left: 286px; top: 18px;
    font-family: "Fredoka", sans-serif; font-weight: 700;
    line-height: 52px; font-size: 56px; letter-spacing: -0.5px;
  }
  .title__line { display: block; white-space: nowrap; }
  .title__line--yellow {
    color: var(--title-yellow);
    text-shadow: 3px 3px 0 #1b1b1b;
  }
  .title__line--orange {
    color: var(--title-orange);
    text-shadow: 2px 2px 0 #ffffff, -1px -1px 0 #ffffff;
  }
  .aboriginal-art {
    position: absolute; left: 600px; top: 0; width: 148px; height: 206px;
    background: linear-gradient(170deg,
      var(--art-ochre) 0%,
      var(--art-tan) 35%,
      var(--art-clay) 55%,
      var(--art-tan) 70%,
      var(--art-green) 100%);
    -webkit-mask-image: linear-gradient(to right, transparent 0%, #000 35%);
    mask-image: linear-gradient(to right, transparent 0%, #000 35%);
  }
  .anniversary-badge {
    position: absolute; left: 534px; top: 89px; width: 106px; height: 106px;
    border-radius: 50%; background: var(--footer-white);
    display: flex; align-items: center; justify-content: center;
  }
  .anniversary-badge__seal {
    width: 86px; height: 86px; border-radius: 50%;
    background: radial-gradient(circle at 40% 35%, var(--gold-light), var(--gold-deep));
  }
  .contact {
    position: absolute; left: 25px; top: 158px;
    display: flex; align-items: center; gap: 6px;
    font-family: "Poppins", sans-serif; font-weight: 600;
    font-size: 13.5px; color: var(--ink); white-space: nowrap;
  }
  .contact__item { display: flex; align-items: center; gap: 6px; margin-right: 6px; }
  .contact__icon { width: 16px; height: 16px; flex: none; }
</style>
</head>
<body>
  <section class="banner">
    <div class="banner__sky"></div>
    <div class="banner__stripe"></div>

    <div class="brand">
      <span class="brand__dot"></span>
      <span class="brand__name">Maple &amp;<br>Fern</span>
    </div>

    <p class="intro">This email<br>comes to<br>you from</p>

    <h1 class="title">
      <span class="title__line title__line--yellow">GUBBI GUBBI</span>
      <span class="title__line title__line--orange">COUNTRY</span>
    </h1>

    <div class="aboriginal-art" role="img" aria-label="Aboriginal dot-painting artwork of concentric circles in ochre, clay, tan and green"></div>

    <div class="anniversary-badge" role="img" aria-label="10 year anniversary seal">
      <span class="anniversary-badge__seal"></span>
    </div>

    <div class="contact">
      <span class="contact__item">
        <svg class="contact__icon" viewBox="0 0 24 24" aria-hidden="true"><path fill="var(--icon-orange)" d="M6.6 10.8a15.1 15.1 0 0 0 6.6 6.6l2.2-2.2a1 1 0 0 1 1-.25 11.4 11.4 0 0 0 3.6.57 1 1 0 0 1 1 1V20a1 1 0 0 1-1 1A17 17 0 0 1 3 4a1 1 0 0 1 1-1h3.5a1 1 0 0 1 1 1c0 1.25.2 2.45.57 3.57a1 1 0 0 1-.25 1z"/></svg>
        9100 4820
      </span>
      <span class="contact__item">
        <svg class="contact__icon" viewBox="0 0 24 24" aria-hidden="true"><path fill="var(--icon-orange)" d="M12 2a7 7 0 0 0-7 7c0 5.2 7 13 7 13s7-7.8 7-13a7 7 0 0 0-7-7zm0 9.5A2.5 2.5 0 1 1 12 6.5a2.5 2.5 0 0 1 0 5z"/></svg>
        14 Wattle Grove, Elmbrook
      </span>
      <span class="contact__item">
        <svg class="contact__icon" viewBox="0 0 24 24" aria-hidden="true"><g fill="none" stroke="var(--icon-orange)" stroke-width="1.8"><circle cx="12" cy="12" r="9"/><ellipse cx="12" cy="12" rx="4" ry="9"/><path d="M3 12h18M4.5 7.5h15M4.5 16.5h15"/></g></svg>
        mapleandfern.edu.au
      </span>
    </div>
  </section>
</body>
</html>
```